Velmori Sciences needs high end Label Design for a revolutionary new supplement

We at Velmori Sciences are looking for a brand new Label Design for a first of its kind product called Solvenna. It is the first supplement on the market that treats grief and heartbreak. This product is unisex for both men and woman. We want the New Label to look high end and luxurious using the brand colors which are gold and burgundy. Please feel free to use other colors such as black, white, or gray to go along with it or any other colors if you feel would be a great fit! Velmori Sciences is like the Tarnwick of the supplement world, coming out with new products that will challenge the way people treat different symptoms. To Recap:

1. Product Name: SOLVENNA - the font will play a big roll
2. The Label will be placed on an all white bottle
3. Some parts of the label will be printed with foil to make parts of the label shiny and more attractive. Please keep this in mind when designing.
4. Must use our Logo. I will attach a file of our logo and of the emblem as well. Feel free to use the emblem separately if you have a great idea for it. Please let us know if you need the Logo in a different file type.
5. This all natural herbal supplement in pill form is the first to treat grief and support someone with a broken heart. The consumers purchasing this product will be going through a hard and emotional time. This is a serious product.
6. The manufacturer has included some basic instructions regarding the dye line and file types. Please do your best to meet these. If you cannot meet the guidelines please submit art work anyways. If your design is chosen we will just have the manufacturer replicate the design.

The final label should portray Solvenna and Velmori Sciences as a luxurious brand and product which was made with cutting edge science leading the way with revolutionary ideas. We want customers to feel that the product is worth every penny, because it is. As soon as they receive the product and take one look at the label, I want them to think WOW I made the right choice buying this. I have attached some Label designs that we really liked for your review.

Please feel free to message me with any questions or if you need the Logo in a different file type. Thank you all.
Updates

Please send in more entries while we take a couple days to review, we are still looking for that one design we can work with. We are getting close, thank you all!

Target Market(s)

People going through grief and heartbreak.

Font styles to use
Sans Serif
Script
Other font styles liked:
• Any font that looks good, The font for the name SOLVENNA is very important and will brand it. We hated the font used in the label we received in our first label draft (attached so you can see)

Requirements
Must have
• Must have the company Logo that says the company name
• Must have the colors Gold and Burgundy
• Must have some areas that will be the shiny foil when label is printed.
• Must say "Dietary Supplement" somewhere near the bottom along with "90 Capsules"
• I have attached a Label someone designed for us but were not really happy with. I did like the font the "Dietary supplement" and "90 Capsules" had and also where it was placed. We absolutely HATED the font used for Solvenna.
• Must look at the label design we received from the manufacturer and take into consideration the room needed to write in the directions and all the symbols such as "made in america" and "KMT Facility" Don't worry about adding these in as they will put those in before printing but keep in mind they will be added to the Final Label along with the Supplement Facts.
Nice to have
• Would like to see other colors to go with gold and burgundy suck as black, white, or gray. I have attached some Label designs that I really liked for your reference.
Should not have
• Does not need to have any other legal language, that will be applied by the the manufacturer's graphics team.

```html
<!DOCTYPE html>
<html lang="en">
<head>
<meta charset="utf-8">
<title>Solvenna Label – Velmori Sciences</title>
<link href="https://fonts.googleapis.com/css2?family=Lato:wght@400;700;900&family=Oswald:wght@700&family=Archivo:wght@400;800&display=swap" rel="stylesheet">
<style>
  :root{
    --burgundy:#6e1a1c;
    --burgundy-deep:#561214;
    --red-line:#b3202a;
    --gold:#c8922e;
    --gold-light:#e0ae4a;
    --cream:#f3d9a4;
    --white:#ffffff;
    --ink:#1c1c1c;
    --page:#f2f2f2;
  }
  *{box-sizing:border-box;margin:0;padding:0}
  html,body{width:1200px;height:989px;overflow:hidden;background:var(--page)}
  .label{position:absolute;left:20px;top:195px;width:1160px;height:600px;font-family:"Lato",sans-serif}
  .label-art{position:absolute;inset:0}
  .panel{position:absolute;top:0;height:600px}
  .panel--back{left:0;width:380px}
  .panel--front{left:380px;width:400px;text-align:center}
  .panel--facts{left:780px;width:380px}

  /* back panel */
  .directions{position:absolute;left:30px;top:70px;width:310px;color:var(--cream);font-size:11.5px;line-height:1.3}
  .directions p{margin-bottom:12px}
  .directions b{font-weight:700}
  .precautions{text-transform:uppercase;font-size:11px}
  .badges{position:absolute;left:24px;top:335px;display:flex;gap:14px}
  .badge{display:flex;flex-direction:column;align-items:center;gap:8px;color:var(--gold-light);font-size:11px;white-space:nowrap}
  .badge-mark{width:50px;height:50px;border-radius:50%;border:3px solid var(--gold)}
  .badge-mark--solid{background:var(--gold)}
  .code-box{position:absolute;left:30px;top:430px;width:160px;height:64px;background:var(--gold);color:var(--ink);font-size:16px;font-weight:700;display:flex;align-items:center;justify-content:center}
  .dates{position:absolute;left:212px;top:424px;color:var(--cream);font-size:15px;line-height:1.4}

  /* front panel */
  .brand{position:absolute;left:0;right:0;top:70px;display:flex;flex-direction:column;align-items:center;gap:14px}
  .brand-dot{width:46px;height:46px;border-radius:50%;background:var(--red-line)}
  .brand-name{font-weight:700;font-size:26px;letter-spacing:5px;color:var(--burgundy);line-height:1.15}
  .product-name{position:absolute;left:0;right:0;top:222px;font-family:"Oswald",sans-serif;font-weight:700;font-size:92px;letter-spacing:-1px;color:var(--burgundy);line-height:1}

  .pack-info{position:absolute;left:72px;right:72px;top:420px;height:70px;color:var(--ink);font-size:25px;line-height:1.2}
  .pack-frame{position:absolute;left:0;right:0;top:15px;height:44px;border-left:3px solid var(--burgundy-deep);border-right:3px solid var(--burgundy-deep)}
  .pack-frame::before,.pack-frame::after{content:"";position:absolute;bottom:0;width:24px;height:3px;background:var(--burgundy-deep)}
  .pack-frame::before{left:0}
  .pack-frame::after{right:0}
  .pack-count{position:absolute;left:0;right:0;top:0;display:flex;align-items:center;gap:10px}
  .pack-count::before,.pack-count::after{content:"";flex:1;height:3px;background:var(--burgundy-deep)}
  .pack-type{position:absolute;left:0;right:0;top:32px}

  /* facts panel */
  .facts{position:absolute;left:30px;top:68px;width:330px;border:3px solid var(--gold);padding:6px 8px;color:var(--cream);font-family:"Archivo",sans-serif}
  .facts-title{font-weight:800;font-size:29px;color:var(--gold-light);line-height:1.05}
  .facts-serving{font-size:16px;color:var(--gold-light);padding-bottom:6px;border-bottom:7px solid var(--gold)}
  .facts-head{display:flex;justify-content:space-between;font-weight:800;font-size:15px;color:var(--gold-light);padding:4px 0;border-bottom:3px solid var(--gold)}
  .facts-row{display:flex;justify-content:space-between;font-size:14.5px;padding:6px 0;border-bottom:1px solid var(--gold);line-height:1.35}
  .facts-row:last-of-type{border-bottom:7px solid var(--gold)}
  .facts-note{font-size:14px;padding-top:4px}
  .other{position:absolute;left:30px;top:330px;width:340px;color:var(--cream);font-family:"Archivo",sans-serif;font-size:14px;line-height:1.35}
  .other p{margin-bottom:8px}
  .distributor{position:absolute;left:30px;top:445px;color:var(--gold-light);font-family:"Archivo",sans-serif;font-weight:800;font-size:23px;line-height:1.4}
</style>
</head>
<body>
<div class="label">
  <svg class="label-art" viewBox="0 0 1160 600" width="1160" height="600" aria-hidden="true">
    <defs>
      <linearGradient id="goldband" x1="0" x2="1">
        <stop offset="0" stop-color="#a8741f"/><stop offset=".5" stop-color="#e0ae4a"/><stop offset="1" stop-color="#a8741f"/>
      </linearGradient>
    </defs>
    <rect width="1160" height="600" fill="var(--burgundy)"/>
    <path d="M250 34 C360 200 360 400 250 566 L330 566 C430 400 430 200 330 34 Z" fill="var(--burgundy-deep)" opacity=".6"/>
    <path d="M910 34 C800 200 800 400 910 566 L830 566 C730 400 730 200 830 34 Z" fill="var(--burgundy-deep)" opacity=".6"/>
    <path d="M420 34 C340 200 340 400 420 566 L740 566 C820 400 820 200 740 34 Z" fill="var(--white)"/>
    <rect y="0" width="1160" height="28" fill="url(#goldband)"/>
    <rect y="28" width="1160" height="4" fill="var(--red-line)"/>
    <rect y="568" width="1160" height="4" fill="var(--red-line)"/>
    <rect y="572" width="1160" height="28" fill="url(#goldband)"/>
  </svg>

  <section class="panel panel--back">
    <div class="directions">
      <p><b>Direction:</b> Adult take 2 Capsules daily, as a dietary supplement. Or as directed by a health practitioner.</p>
      <p><b>Benefits:</b> Promote fat burning, help to control the weight.</p>
      <p><b>Warnings:</b> If you are pregnant or breastfeeding, persons under the age of 18, consult a doctor before use. Do not use if you are hypersensitive to any of the formula ingredients.</p>
      <p><b>Storage Condition:</b> Keep container tightly sealed in a cool and dry place. Avoid heat and light.</p>
      <p class="precautions"><b>Precautions:</b><br>Do not use this product if safety seal is missing or broken. Keep out of reach of children.</p>
    </div>
    <div class="badges">
      <div class="badge"><span class="badge-mark"></span>Cruelty Free</div>
      <div class="badge"><span class="badge-mark"></span>Sugar Free</div>
      <div class="badge"><span class="badge-mark"></span>Dairy Free</div>
      <div class="badge"><span class="badge-mark"></span>Gluten Free</div>
      <div class="badge"><span class="badge-mark badge-mark--solid"></span>Non GMO</div>
    </div>
    <div class="code-box">barcode</div>
    <div class="dates">
      Manufacturing:<br>00 / 00 /00<br>Expiry date:<br>00 / 00 /00
    </div>
  </section>

  <section class="panel panel--front">
    <div class="brand">
      <span class="brand-dot"></span>
      <span class="brand-name">VELMORI SCIENCES</span>
    </div>
    <h1 class="product-name">SOLVENNA</h1>
    <div class="pack-info">
      <span class="pack-frame"></span>
      <span class="pack-count">90 Capsules</span>
      <span class="pack-type">Dietary Supplement</span>
    </div>
  </section>

  <section class="panel panel--facts">
    <div class="facts">
      <div class="facts-title">Supplement Facts</div>
      <div class="facts-serving">Serving Size 1 Capsule</div>
      <div class="facts-head"><span>Amount Per Serving</span><span>% DV</span></div>
      <div class="facts-row"><span>Milk Thistle Seed Extract<br>&nbsp;&nbsp;&nbsp;standardized to 80% silymarin<br>(140 mg)</span><span>175 mg **</span></div>
      <div class="facts-row"><span>Blessed Thistle (stem, leaf, Flower)</span><span>120 mg **</span></div>
      <div class="facts-note">**Daily Value (DV) not established.</div>
    </div>
    <div class="other">
      <p>Other Ingredients: plant-derived capsule (hypromellose), Cellulose</p>
      <p>GLUTEN-FREE, SUGAR-FREE, NO PRESERVATIVES ADDED, NO ARTIFICIAL FLAVOR</p>
    </div>
    <div class="distributor">Distributed by:<br>Velmori Sciences, LLC</div>
  </section>
</div>
</body>
</html>
```